red maple heating & air company flyer for listbazaar ad

size should be 1200x900
this is an ac company, we have a logo but not necessary to use
we offer free estimates, we are open 24/7, fast and affordable
service, licensed and insured
we sell all brands and service all
we offer services for refrigeration residential and commercial
I will post a few of my ads I made but need a pros idea

Red Maple Heating & Air Company
407-318-5274
redmapleair@quorvanmail.com
redmapleair247.com
license # must be on flyer state law it is CAC2739561
if you use the logo please remove the building

Target Market(s)

any one who needs has an ac in home

Industry/Entity Type

Hvac

Requirements
Must have
• contact info must be big

```html
<!DOCTYPE html>
<html lang="en">
<head>
<meta charset="utf-8">
<title>Red Maple Heating &amp; Air Company</title>
<link rel="stylesheet" href="https://fonts.googleapis.com/css2?family=Oswald:wght@500;600;700&family=Lato:ital,wght@0,700;0,900;1,700;1,900&display=swap">
<style>
  :root {
    --blue: #2e3191;
    --red: #d5232a;
    --ink: #3b3b3b;
    --black: #151515;
    --white: #ffffff;
    --unit-dark: #2f3230;
    --unit-mid: #5a5e5b;
  }
  * { margin: 0; padding: 0; box-sizing: border-box; }
  html, body { width: 1200px; height: 902px; overflow: hidden; background: var(--white); }
  .flyer { position: relative; width: 1200px; height: 902px; overflow: hidden; background: var(--white); font-family: "Lato", sans-serif; }
  .backdrop { position: absolute; inset: 0; }
  .headline-company {
    position: absolute; top: 26px; left: 0; width: 1200px; text-align: center;
    font-family: "Oswald", sans-serif; font-weight: 600; font-size: 68px; line-height: 1;
    color: var(--blue); white-space: nowrap;
    transform: scaleX(0.73); transform-origin: 600px 0;
  }
  .headline-company .accent { color: var(--red); }
  .offer-title {
    position: absolute; top: 151px; left: 41px;
    font-family: "Oswald", sans-serif; font-weight: 600; font-size: 68px; line-height: 1;
    color: var(--ink); white-space: nowrap;
    transform: scaleX(0.9); transform-origin: 0 0;
  }
  .offer-title .accent { color: var(--red); }
  .benefits { position: absolute; top: 246px; left: 47px; list-style: none; }
  .benefits li {
    position: relative; padding-left: 46px; height: 50px;
    font-style: italic; font-weight: 900; font-size: 33px; line-height: 38px; color: var(--black); white-space: nowrap;
  }
  .benefits li::before {
    content: ""; position: absolute; left: 0; top: 9px; width: 21px; height: 21px;
    border-radius: 50%; background: var(--blue);
  }
  .refrigeration-title {
    position: absolute; top: 424px; left: 41px;
    font-style: italic; font-weight: 900; font-size: 37px; line-height: 46px; color: var(--red); white-space: nowrap;
  }
  .refrigeration-type {
    position: absolute; top: 478px;
    font-style: italic; font-weight: 900; font-size: 29px; line-height: 34px; color: var(--black); white-space: nowrap;
  }
  .refrigeration-type.residential { left: 95px; }
  .refrigeration-type.commercial { left: 344px; }
  .tick-box { position: absolute; top: 483px; }
  .tick-box.residential { left: 38px; }
  .tick-box.commercial { left: 290px; }
  .open-badge-text {
    position: absolute; top: 186px; left: 772px;
    font-style: italic; font-weight: 900; font-size: 45px; line-height: 52px; color: var(--white); white-space: nowrap;
  }
  .open-badge-hours {
    position: absolute; top: 200px; left: 1077px; width: 70px; text-align: center;
    font-weight: 900; font-size: 25px; line-height: 32px; color: var(--red);
  }
  .phone {
    position: absolute; top: 568px; left: 128px;
    font-family: "Oswald", sans-serif; font-weight: 700; font-size: 84px; line-height: 1;
    color: var(--black); letter-spacing: 2px; white-space: nowrap;
  }
  .license {
    position: absolute; top: 679px; left: 157px; width: 379px; height: 50px;
    text-align: center; line-height: 50px;
    font-weight: 900; font-size: 29px; color: var(--white); white-space: nowrap;
  }
  .contact { position: absolute; left: 40px; top: 764px; list-style: none; }
  .contact li {
    display: flex; align-items: center; gap: 20px; height: 50px;
    font-weight: 900; font-size: 31px; color: var(--white); white-space: nowrap;
  }
  .product-photo {
    position: absolute; left: 696px; top: 391px; width: 482px; height: 468px;
    background: linear-gradient(160deg, var(--unit-mid) 0%, var(--unit-dark) 70%);
    border-radius: 6px;
  }
</style>
</head>
<body>
<main class="flyer">
  <svg class="backdrop" width="1200" height="902" viewBox="0 0 1200 902" aria-hidden="true">
    <defs>
      <linearGradient id="header-fade" x1="0" y1="0" x2="0" y2="1">
        <stop offset="0" stop-color="#ffffff"/>
        <stop offset="1" stop-color="#e4e4e6"/>
      </linearGradient>
      <linearGradient id="swoosh" x1="0" y1="0" x2="1" y2="0">
        <stop offset="0" stop-color="#d8d8da"/>
        <stop offset="1" stop-color="#c4c4c7"/>
      </linearGradient>
    </defs>
    <path d="M0 0 H1200 V100 Q1200 113 1170 115 Q1110 118 1070 118 H110 Q40 118 0 80 Z" fill="url(#header-fade)"/>
    <path d="M0 410 H538 Q586 410 586 460 V474 Q586 524 538 524 H0" fill="var(--white)" stroke="var(--blue)" stroke-width="4"/>
    <path d="M0 700 Q220 740 720 700 L720 740 Q300 770 0 745 Z" fill="url(#swoosh)"/>
    <path d="M0 680 Q260 730 720 688" fill="none" stroke="var(--red)" stroke-width="6"/>
    <path d="M0 752 Q300 775 720 748 V902 H0 Z" fill="var(--blue)"/>
    <circle cx="1030" cy="710" r="390" fill="var(--blue)"/>
    <circle cx="1030" cy="710" r="378" fill="var(--white)"/>
    <circle cx="1030" cy="710" r="366" fill="var(--red)"/>
    <path d="M797 166 H1070 V264 H797 Q747 264 747 215 Q747 166 797 166 Z" fill="var(--blue)"/>
    <circle cx="1112" cy="216" r="77" fill="var(--red)"/>
    <circle cx="1112" cy="216" r="53" fill="var(--white)"/>
    <circle cx="1112" cy="216" r="44" fill="none" stroke="var(--red)" stroke-width="3"/>
    <g stroke="var(--white)" stroke-width="5">
      <line x1="1112" y1="139" x2="1112" y2="159"/>
      <line x1="1112" y1="273" x2="1112" y2="293"/>
      <line x1="1035" y1="216" x2="1055" y2="216"/>
      <line x1="1169" y1="216" x2="1189" y2="216"/>
    </g>
    <rect x="157" y="679" width="379" height="50" rx="25" fill="var(--red)"/>
    <circle cx="66" cy="610" r="31" fill="none" stroke="var(--red)" stroke-width="5"/>
    <path d="M54 592 q-6 4 -3 14 q6 16 20 24 q9 4 13 -2 l-7 -8 q-4 3 -7 1 q-7 -5 -11 -13 q-1 -4 3 -6 Z" fill="var(--red)"/>
  </svg>

  <h1 class="headline-company">RED MAPLE HEATING <span class="accent">&amp; AIR COMPANY</span></h1>

  <h2 class="offer-title"><span class="accent">WE OFFER</span> FREE ESTIMATES</h2>

  <ul class="benefits">
    <li>Fast and affordable service</li>
    <li>Licensed and insured</li>
    <li>We sell all brands and service all</li>
  </ul>

  <section class="refrigeration">
    <p class="refrigeration-title">We offer services for refrigeration</p>
    <svg class="tick-box residential" width="22" height="22" viewBox="0 0 22 22" aria-hidden="true"><rect x="1.5" y="5.5" width="15" height="15" fill="none" stroke="var(--blue)" stroke-width="2.5"/><path d="M4 12 l5 5 l11 -15" fill="none" stroke="var(--blue)" stroke-width="3"/></svg>
    <span class="refrigeration-type residential">Residential</span>
    <svg class="tick-box commercial" width="22" height="22" viewBox="0 0 22 22" aria-hidden="true"><rect x="1.5" y="5.5" width="15" height="15" fill="none" stroke="var(--blue)" stroke-width="2.5"/><path d="M4 12 l5 5 l11 -15" fill="none" stroke="var(--blue)" stroke-width="3"/></svg>
    <span class="refrigeration-type commercial">Commercial</span>
  </section>

  <p class="open-badge-text">We are open</p>
  <p class="open-badge-hours">24/7</p>

  <p class="phone">407-318-5274</p>

  <p class="license">License # CAC2739561</p>

  <ul class="contact">
    <li><svg width="36" height="30" viewBox="0 0 36 30" aria-hidden="true"><path d="M3 12 L18 2 L33 12 V28 H3 Z" fill="none" stroke="var(--white)" stroke-width="2.5"/><path d="M3 12 L18 22 L33 12" fill="none" stroke="var(--white)" stroke-width="2.5"/></svg>redmapleair@quorvanmail.com</li>
    <li><svg width="36" height="30" viewBox="0 0 36 30" aria-hidden="true"><g fill="none" stroke="var(--white)" stroke-width="2.2"><circle cx="18" cy="15" r="12"/><ellipse cx="18" cy="15" rx="5" ry="12"/><line x1="6" y1="15" x2="30" y2="15"/><line x1="8" y1="9" x2="28" y2="9"/><line x1="8" y1="21" x2="28" y2="21"/></g></svg>www.redmapleair247.com</li>
  </ul>

  <div class="product-photo" role="img" aria-label="Photo of an outdoor air conditioner condenser unit beside an indoor air handler cabinet"></div>
</main>
</body>
</html>
```